To design a brand identity that is simple and creative with 'Corvane' as the brand name, I like modern simple fonts like helvetica neue, I want to print both sides of the card, I am open to dark front and white back, but the design needs to transfer well to letter heads and email signatures, I am looking for sophisticated and elegant, but open minded about clever and off the wall, I do not do 'boring' Corvane Ventures is the mother company for a small group, specialising in Management & consulting, Software development and construction, we have a high level of integrity, we are transparent and accountable for what we do. my images are provided as a guide only, Im not expecting them to be just copied, Im looking for a creator and passionate thinker, who will put life into their work.

Target Market(s)

usually business minded people who are looking for something different in me, such as leadership, confidence and focus with thinking that is per haps a little outside the box..

Industry/Entity Type

Construction

Requirements
Must have
• clean, minmalistic
Nice to have
• custom logo
Should not have
• boring, traditional

```html
<!DOCTYPE html>
<html lang="en">
<head>
<meta charset="utf-8">
<title>Corvane Business Card</title>
<link rel="stylesheet" href="https://fonts.googleapis.com/css2?family=Lato:wght@300;400;700&display=swap">
<style>
  :root {
    --canvas: #ecebe8;
    --card-dark: #1c1c1e;
    --card-dark-edge: #2a2a2d;
    --card-light: #ffffff;
    --orange: #e8622c;
    --white: #ffffff;
    --muted: #d9d9d9;
    --accent-yellow: #f6b21a;
    --accent-red: #e8372f;
    --accent-magenta: #b3287c;
    --accent-teal: #2aa6a0;
  }
  * { box-sizing: border-box; margin: 0; padding: 0; }
  html, body {
    width: 1200px;
    height: 720px;
    overflow: hidden;
    background: var(--canvas);
    font-family: "Lato", "Helvetica Neue", Arial, sans-serif;
  }
  .canvas {
    position: relative;
    width: 1200px;
    height: 720px;
  }
  .card {
    position: absolute;
    top: 205px;
    width: 540px;
    height: 310px;
    overflow: hidden;
    box-shadow: 0 10px 28px rgba(0, 0, 0, 0.18);
  }
  /* Front */
  .card--front {
    left: 45px;
    background: linear-gradient(160deg, var(--card-dark-edge) 0%, var(--card-dark) 55%, #141415 100%);
  }
  .card__art {
    position: absolute;
    inset: 0;
    width: 100%;
    height: 100%;
  }
  .brand {
    position: absolute;
    left: 40px;
    top: 38px;
    display: flex;
    align-items: center;
    gap: 22px;
  }
  .brand__dot {
    width: 58px;
    height: 58px;
    border-radius: 50%;
    background: var(--orange);
  }
  .brand__name {
    font-weight: 300;
    font-size: 66px;
    line-height: 1;
    color: var(--orange);
    letter-spacing: 1px;
  }
  .address {
    position: absolute;
    right: 26px;
    top: 184px;
    font-size: 13px;
    color: var(--white);
    letter-spacing: 0.2px;
  }
  .person {
    position: absolute;
    left: 40px;
    top: 205px;
    font-size: 13px;
    color: var(--white);
  }
  .person__name {
    font-weight: 700;
    font-size: 17px;
    color: var(--orange);
  }
  .contact {
    position: absolute;
    left: 40px;
    top: 236px;
    list-style: none;
    font-size: 12.5px;
    color: var(--muted);
  }
  .contact__item {
    display: flex;
    align-items: center;
    gap: 7px;
    height: 22px;
  }
  .contact__icon {
    width: 12px;
    height: 12px;
    flex: none;
  }
  /* Back */
  .card--back {
    left: 615px;
    background: var(--card-light);
  }
  .wordmark {
    position: absolute;
    left: 0;
    right: 0;
    top: 72px;
    text-align: center;
    font-weight: 300;
    font-size: 112px;
    line-height: 1;
    color: var(--orange);
    letter-spacing: 2px;
  }
  .services {
    position: absolute;
    left: 0;
    right: 0;
    bottom: 44px;
    text-align: center;
    font-weight: 400;
    font-size: 18px;
    color: var(--orange);
    letter-spacing: 0.3px;
  }
</style>
</head>
<body>
<main class="canvas">

  <section class="card card--front" aria-label="Card front">
    <svg class="card__art" viewBox="0 0 540 310" aria-hidden="true">
      <defs>
        <linearGradient id="strip-gradient" x1="0" y1="0" x2="1" y2="0">
          <stop offset="0" stop-color="var(--accent-yellow)"/>
          <stop offset="0.45" stop-color="var(--accent-red)"/>
          <stop offset="0.8" stop-color="var(--accent-magenta)"/>
          <stop offset="1" stop-color="var(--accent-magenta)" stop-opacity="0.2"/>
        </linearGradient>
      </defs>
      <polygon class="address-band" points="308,174 540,160 540,198 296,210" fill="var(--orange)"/>
      <polygon class="accent-triangle" points="282,214 300,212 290,230" fill="var(--accent-teal)"/>
      <polygon class="colour-strip" points="0,292 260,288 300,282 300,296 0,302" fill="url(#strip-gradient)"/>
    </svg>

    <div class="brand">
      <span class="brand__dot"></span>
      <span class="brand__name">corvane.</span>
    </div>

    <p class="address">Po Box 318 Harlow 6104</p>

    <p class="person"><span class="person__name">Your Name,</span> Title</p>

    <ul class="contact">
      <li class="contact__item">
        <svg class="contact__icon" viewBox="0 0 12 12" aria-hidden="true">
          <circle cx="6" cy="6" r="6" fill="var(--orange)"/>
          <path d="M4 3.2 L5 3 L5.6 4.6 L5 5.1 C5.4 6 6 6.6 6.9 7 L7.4 6.4 L9 7 L8.8 8 C6.2 8.2 3.8 5.8 4 3.2 Z" fill="var(--white)"/>
        </svg>
        +61 0400 512 947
      </li>
      <li class="contact__item">
        <svg class="contact__icon" viewBox="0 0 12 12" aria-hidden="true">
          <rect x="0" y="1.5" width="12" height="9" rx="1.5" fill="var(--orange)"/>
          <path d="M1.5 3 L6 6.5 L10.5 3" stroke="var(--white)" stroke-width="1" fill="none"/>
        </svg>
        Names@corvane.ventures
      </li>
    </ul>
  </section>

  <section class="card card--back" aria-label="Card back">
    <p class="wordmark">corvane.</p>
    <p class="services">Management • Software • Construction</p>
  </section>

</main>
</body>
</html>
```